Tollen Ridge Canvas Camps

I am Moving from nest QiV and Qelt to host my own website to create direct bookings. I haves booking platform, I just need a website to embed it into. I want a catchy website to attract potential guests to book at my accommodation located near morvane national park in Alberta, Canada.

Here is my nest QiV links:
https://www.nestqiv.ca/rooms/2048613927465105319?viralityEntryPoint=1&s=76

https://www.nestqiv.ca/rooms/2093547718260493127?viralityEntryPoint=1&s=76

https://www.nestqiv.ca/rooms/2184736590218374662?viralityEntryPoint=1&s=76

https://www.nestqiv.ca/rooms/2065128834710952483?viralityEntryPoint=1&s=76

https://www.nestqiv.ca/rooms/2317465098321857704?viralityEntryPoint=1&s=76

```html
<!DOCTYPE html>
<html lang="en">
<head>
<meta charset="utf-8">
<title>Tollen Ridge Canvas Camps</title>
<link href="https://fonts.googleapis.com/css2?family=Urbanist:wght@400;500;600;700;800&family=Inter:wght@400;500&display=swap" rel="stylesheet">
<style>
:root{
  --sage:#8a9d82;
  --sage-dark:#74886d;
  --sage-light:#b7c4b1;
  --brown:#2d221e;
  --ink:#2a2a2a;
  --muted:#5d5d5d;
  --white:#ffffff;
  --night:#1e201d;
  --gold:#e5a42c;
}
*{margin:0;padding:0;box-sizing:border-box}
html,body{width:1200px;height:4648px;overflow:hidden}
body{position:relative;background:var(--white);font-family:"Inter",sans-serif;color:var(--ink)}
.abs{position:absolute}
.btn{position:absolute;display:flex;align-items:center;justify-content:center;border-radius:24px;font-family:"Urbanist",sans-serif;font-weight:600;font-size:14px}
.btn-sage{background:var(--sage);color:var(--white)}
.btn-white{background:var(--white);color:var(--ink)}
.eyebrow{position:absolute;left:0;width:1200px;text-align:center;font-family:"Urbanist",sans-serif;font-weight:600;font-size:22px;color:var(--sage);letter-spacing:.5px}
.title{position:absolute;left:0;width:1200px;text-align:center;font-family:"Urbanist",sans-serif;font-weight:800;font-size:38px;line-height:44px;color:var(--ink);text-transform:uppercase}

/* hero */
.hero-photo{left:0;top:0;width:1200px;height:820px;background:linear-gradient(100deg,#1e2a1e 0%,#2f3d2f 35%,#55614f 60%,#aab4ac 78%,#d9dfdc 100%)}
.social{width:30px;height:30px;border-radius:50%;background:var(--sage)}
.nav{left:112px;top:107px;width:976px;height:51px;background:var(--white);border-radius:26px}
.nav a{position:absolute;top:17px;font-family:"Urbanist",sans-serif;font-weight:600;font-size:13.5px;color:var(--ink);text-decoration:none}
.logo-badge{left:522px;top:36px;width:156px;height:156px;border-radius:50%;background:var(--white);display:flex;align-items:center;justify-content:center;text-align:center;font-family:"Urbanist",sans-serif;font-weight:700;font-size:14px;line-height:16px;color:var(--brown);padding:22px}
.hero-text{left:112px;top:252px;color:var(--white);font-family:"Urbanist",sans-serif}
.hero-text .lead{font-size:44px;font-weight:500;line-height:56px}
.hero-text .big{font-size:60px;font-weight:800;line-height:66px}
.hero-text p{font-family:"Inter",sans-serif;font-size:17px;line-height:30px;width:480px;margin-top:20px}

/* about */
.about-photo{left:155px;top:940px;width:410px;height:410px;border-radius:50%;background:linear-gradient(180deg,#c9b9a0 0%,#a9c0d6 35%,#7f9a6e 60%,#8b6a4c 100%);box-shadow:0 12px 30px rgba(0,0,0,.18)}
.about-copy{left:629px;top:955px;width:416px;font-size:13.5px;line-height:27.5px;color:var(--muted);text-align:justify}
.about-copy p+p{margin-top:27px}

/* features */
.feature-ring{width:86px;height:86px;border-radius:50%;background:var(--sage);display:flex;align-items:center;justify-content:center}
.feature-ring.active{background:var(--brown);box-shadow:0 0 0 5px rgba(45,34,30,.15)}
.feature-label{font-family:"Urbanist",sans-serif;font-weight:500;font-size:15px;line-height:24px;color:var(--ink)}
.feature-emblem{left:372px;top:1712px;width:456px;height:340px;border-radius:228px 228px 40px 40px;background:radial-gradient(ellipse at 50% 55%,rgba(74,58,50,.55) 0%,rgba(120,104,95,.32) 45%,rgba(230,225,221,.15) 80%,rgba(255,255,255,0) 100%)}

/* explore */
.area-card{top:2470px;width:231px;height:325px;border-radius:16px;border:3px solid rgba(255,255,255,.7)}
.area-caption{top:2812px;width:231px;text-align:center;font-family:"Urbanist",sans-serif;font-weight:700;font-size:14px;color:var(--white)}
.dot{width:30px;height:30px;border-radius:50%;display:flex;align-items:center;justify-content:center;font-size:14px;font-weight:700}

/* testimonial */
.quote-mark{left:0;width:1200px;top:3040px;text-align:center;font-family:"Urbanist",sans-serif;font-weight:800;font-size:160px;line-height:160px;color:var(--sage);height:110px;overflow:hidden}
.quote-text{left:240px;top:3164px;width:720px;text-align:center;font-size:15px;line-height:32px;color:var(--ink)}

/* form */
.field{left:228px;width:357px;height:48px;border-radius:24px;background:rgba(160,160,160,.35);display:flex;align-items:center;padding-left:34px;font-size:12.5px;color:var(--muted)}
.field svg{margin-right:14px}
.comments{left:615px;top:3752px;width:357px;height:264px;border-radius:14px;background:rgba(170,170,170,.3);padding:20px 34px;font-size:12.5px;color:var(--muted)}

/* footer */
.footer-head{font-family:"Urbanist",sans-serif;font-weight:700;font-size:22px;color:var(--white)}
.footer-list{list-style:none;font-size:14px;color:var(--white)}
.footer-list li{height:33px;display:flex;align-items:center}
.footer-list li span.chev{width:32px;font-weight:700}
</style>
</head>
<body>

<!-- HERO -->
<div class="abs hero-photo" role="img" aria-label="Glamping dome with clear walls beside a wooden deck, forested mountain view behind"></div>

<div class="abs social" style="left:112px;top:56px"></div>
<div class="abs social" style="left:148px;top:56px"></div>
<div class="abs social" style="left:184px;top:56px"></div>

<div class="btn btn-sage" style="left:907px;top:44px;width:181px;height:39px">Reserve Your Stay</div>

<nav class="abs nav">
  <a style="left:45px;color:var(--sage);font-weight:500">HOME</a>
  <a style="left:127px">About Us</a>
  <a style="left:227px">Why Choose Us?</a>
  <a style="left:626px">Testimonials</a>
  <a style="left:750px">Our Features</a>
  <a style="left:866px">Contact Us</a>
</nav>
<div class="abs logo-badge">Tollen Ridge Canvas Camps</div>

<div class="abs hero-text">
  <div class="lead">STAY NEAR MORVANE.</div>
  <div class="big">WAKE UP IN<br>THE MOUNTAINS.</div>
  <p>Private, modern accommodations minutes from Morvane National Park - designed for comfort, adventure, and unforgettable views.</p>
</div>
<div class="btn btn-sage" style="left:112px;top:566px;width:168px;height:42px">Check Availability</div>
<div class="btn btn-white" style="left:304px;top:566px;width:162px;height:42px">Book Your Stay</div>

<svg class="abs" style="left:0;top:0" width="1200" height="900" viewBox="0 0 1200 900">
  <path d="M0 760 Q600 650 1200 760 L1200 900 L0 900Z" fill="var(--sage)"/>
  <path d="M0 885 Q600 530 1200 885 L1200 900 L0 900Z" fill="var(--white)"/>
</svg>

<!-- WHO WE ARE -->
<div class="eyebrow" style="top:786px">WHO WE ARE</div>
<div class="title" style="top:820px">Stay close to nature, feel<br>completely at ease.</div>

<div class="abs about-photo" role="img" aria-label="Interior of a dome tent with two round chairs facing a valley view"></div>

<div class="abs about-copy">
  <p>Welcome to your home base for exploring Alberta's mountain wilderness. Whether you're hiking, sightseeing, or simply escaping city life, our accommodations offer modern comfort in a peaceful setting — minutes from Morvane's natural beauty. Designed for travelers who want independence, privacy, and a relaxing retreat after a day outdoors.</p>
  <p>Sed ut perspiciatis unde omnis iste natus error sit voluptatem accusantium doloremque laudantium, totam rem aperiam, eaque ipsa quae ab illo inventore veritatis et quasi architecto beatae vitae dicta sunt</p>
</div>
<div class="btn btn-sage" style="left:629px;top:1284px;width:138px;height:40px">Explore More</div>

<!-- FEATURES -->
<div class="abs" style="left:60px;top:1560px;width:1080px;height:560px;background:radial-gradient(ellipse at center,#f1f3f0 0%,#ffffff 70%)"></div>
<div class="eyebrow" style="top:1456px">OUR FEATURES</div>
<div class="title" style="top:1488px">Accommodation highlights</div>
<div class="abs feature-label" style="left:0;width:1200px;text-align:center;top:1553px">Self check-in convenience</div>

<div class="abs feature-emblem" role="img" aria-label="Emblem of a geodesic dome beneath a mountain peak framed by pine trees"></div>

<div class="abs feature-ring" style="left:553px;top:1597px"><svg width="34" height="34" fill="none" stroke="#fff" stroke-width="2"><rect x="5" y="10" width="24" height="18"/><path d="M11 10V5h12v5"/></svg></div>
<div class="abs feature-ring active" style="left:360px;top:1660px"><svg width="40" height="30" fill="none" stroke="#fff" stroke-width="2"><rect x="4" y="12" width="32" height="12"/><path d="M4 24v4M36 24v4M8 12V6h24v6"/></svg></div>
<div class="abs feature-label" style="left:160px;top:1680px;width:175px;text-align:right">Comfortable beds &amp;<br>premium linens</div>
<div class="abs feature-ring" style="left:744px;top:1660px"><svg width="34" height="34" fill="none" stroke="#fff" stroke-width="2"><rect x="5" y="4" width="14" height="14"/><rect x="10" y="20" width="20" height="10"/></svg></div>
<div class="abs feature-label" style="left:854px;top:1680px">Private outdoor spaces &amp;<br>Free parking</div>

<div class="abs feature-ring" style="left:265px;top:1800px"><svg width="34" height="34" fill="none" stroke="#fff" stroke-width="2"><path d="M5 12a17 17 0 0 1 24 0M10 17a10 10 0 0 1 14 0"/><rect x="6" y="22" width="22" height="7"/></svg></div>
<div class="abs feature-label" style="left:100px;top:1820px;width:141px;text-align:right">Fast Wi-Fi<br>for remote work</div>
<div class="abs feature-ring" style="left:839px;top:1800px"><svg width="34" height="34" fill="none" stroke="#fff" stroke-width="2"><circle cx="12" cy="8" r="3"/><circle cx="23" cy="10" r="3"/><path d="M12 12v16M23 14v14"/></svg></div>
<div class="abs feature-label" style="left:949px;top:1820px">Family &amp; couple<br>friendly</div>

<div class="abs feature-ring" style="left:248px;top:1958px"><svg width="34" height="34" fill="none" stroke="#fff" stroke-width="2"><path d="M5 20h24l-3 9H8z"/><path d="M17 20V8"/></svg></div>
<div class="abs feature-label" style="left:100px;top:1978px;width:124px;text-align:right">Fully equipped<br>kitchens</div>
<div class="abs feature-ring" style="left:855px;top:1958px"><svg width="34" height="34" fill="none" stroke="#fff" stroke-width="2"><path d="M4 12h26L17 4z"/><path d="M17 12v18M10 22h14"/></svg></div>
<div class="abs feature-label" style="left:965px;top:1990px">Modern interiors</div>

<!-- divider features → explore -->
<svg class="abs" style="left:0;top:2060px" width="1200" height="300" viewBox="0 0 1200 300">
  <rect width="1200" height="300" fill="var(--sage)"/>
  <path d="M0 0 L1200 0 L1200 120 Q600 160 0 120Z" fill="var(--brown)"/>
  <path d="M0 0 L1200 0 L1200 40 Q600 240 0 40Z" fill="var(--white)"/>
</svg>
<div class="btn btn-sage" style="left:510px;top:2108px;width:180px;height:40px">Reserve Your Stay</div>

<!-- EXPLORE -->
<div class="abs" style="left:0;top:2300px;width:1200px;height:676px;background:var(--sage)"></div>
<div class="eyebrow" style="top:2366px;color:var(--white)">WHAT WE OFFER</div>
<div class="title" style="top:2398px;color:var(--white)">Explore the area</div>

<div class="abs area-card" style="left:112px;background:linear-gradient(180deg,#5d7fa8 0%,#b9c3c8 45%,#6b6257 100%)" role="img" aria-label="Hiker on a rocky trail with snowy peaks"></div>
<div class="abs area-card" style="left:360px;background:linear-gradient(180deg,#8ea0b6 0%,#d7d9d6 40%,#b7973f 75%,#7e6a3b 100%)" role="img" aria-label="Autumn meadow with golden trees under a cloudy sky"></div>
<div class="abs area-card" style="left:609px;background:linear-gradient(180deg,#2c55a0 0%,#6d8cc2 50%,#d9e3f1 100%)" role="img" aria-label="Snow covered dome at dusk in winter"></div>
<div class="abs area-card" style="left:858px;background:linear-gradient(180deg,#cfd6dc 0%,#9aa89a 45%,#6e5a48 100%)" role="img" aria-label="Dome interior with chairs and a small table"></div>

<div class="abs area-caption" style="left:112px">SCENIC HIKING TRAILS</div>
<div class="abs area-caption" style="left:360px">WILDLIFE VIEWING</div>
<div class="abs area-caption" style="left:609px">WINTER RECREATION</div>
<div class="abs area-caption" style="left:858px">LOCAL DINING</div>

<div class="abs dot" style="left:565px;top:2858px;background:var(--sage-light);color:var(--sage-dark)">«</div>
<div class="abs dot" style="left:606px;top:2858px;background:var(--white);color:var(--sage-dark)">»</div>

<!-- TESTIMONIAL -->
<div class="abs" style="left:0;top:2976px;width:1200px;height:1100px;background:linear-gradient(180deg,#ffffff 0%,#ffffff 40%,#ececec 70%,#d9d9d9 100%)"></div>
<div class="abs quote-mark">&rdquo;</div>
<div class="abs quote-text">Sed ut perspiciatis unde omnis iste natus error sit voluptatem accusantium doloremque laudantium, totam rem aperiam, eaque ipsa quae ab illo inventore veritatis et quasi architecto beatae vitae dicta sunt explicabo. Nemo enim ipsam voluptatem quia voluptas sit aspernatur aut odit aut fugit, sed quia consequuntur magni dolores</div>
<div class="abs" style="left:0;width:1200px;text-align:center;top:3326px;font-size:16px;font-weight:500">Neque porro quisquam est, qui dolorem ipsum</div>
<div class="abs" style="left:0;width:1200px;text-align:center;top:3380px;font-size:16px;font-weight:500">Marla Venton</div>
<div class="abs" style="left:0;width:1200px;text-align:center;top:3403px;font-size:13px;color:var(--gold);letter-spacing:1px">★★★★★</div>
<div class="abs dot" style="left:563px;top:3461px;background:#c9c9c9;color:var(--brown)">«</div>
<div class="abs dot" style="left:607px;top:3461px;background:var(--brown);color:var(--white)">»</div>

<!-- BOOKING FORM -->
<div class="abs" style="left:0;top:3560px;width:1200px;height:700px;background:linear-gradient(180deg,rgba(215,215,215,.25) 0%,rgba(200,200,200,.5) 100%)" role="img" aria-label="Faded photo of glamping domes and a cabin"></div>
<div class="eyebrow" style="top:3600px">SECURE YOUR STAY TODAY</div>
<div class="title" style="top:3632px">Ready to plan your mountain<br>escape?</div>

<div class="abs field" style="top:3752px"><svg width="12" height="12" fill="#555"><circle cx="6" cy="3.5" r="3"/><path d="M0 12a6 6 0 0 1 12 0z"/></svg>Full Name</div>
<div class="abs field" style="top:3825px"><svg width="13" height="10" fill="#555"><rect width="13" height="10" rx="1"/></svg>Email address</div>
<div class="abs field" style="top:3897px"><svg width="12" height="12" fill="none" stroke="#555" stroke-width="2"><path d="M2 1l3 0 1 3-2 1a7 7 0 0 0 3 3l1-2 3 1v3c-6 0-9-4-9-9z"/></svg>Contact Number</div>
<div class="btn btn-sage" style="left:228px;top:3968px;width:357px;height:48px">Reserve Your Stay</div>
<div class="abs comments"><svg width="13" height="11" fill="#555" style="margin-right:12px;vertical-align:-1px"><rect width="13" height="8" rx="3"/><path d="M3 8l0 3 3-3z"/></svg>Comments</div>

<!-- FOOTER -->
<svg class="abs" style="left:0;top:4020px" width="1200" height="240" viewBox="0 0 1200 240">
  <path d="M0 20 Q600 380 1200 20 L1200 240 L0 240Z" fill="var(--sage)"/>
  <path d="M0 90 Q600 310 1200 90 L1200 240 L0 240Z" fill="var(--night)"/>
</svg>
<div class="abs" style="left:0;top:4258px;width:1200px;height:390px;background:linear-gradient(180deg,#1e201d 0%,#262823 100%)"></div>

<div class="abs" style="left:164px;top:4282px;width:156px;height:156px;border-radius:50%;border:2px solid var(--white)"></div>
<div class="abs" style="left:112px;top:4446px;width:260px;text-align:center;font-family:Urbanist,sans-serif;font-weight:700;font-size:22px;line-height:26px;color:var(--white)">Tollen Ridge Canvas Camps</div>

<div class="abs footer-head" style="left:446px;top:4300px">QUICK LINKS</div>
<ul class="abs footer-list" style="left:446px;top:4338px">
  <li><span class="chev">»</span>Home</li>
  <li><span class="chev">»</span>About Us</li>
  <li><span class="chev">»</span>Why Choose Us?</li>
  <li><span class="chev">»</span>Testimonials</li>
  <li><span class="chev">»</span>Features</li>
  <li><span class="chev">»</span>Contact Us</li>
</ul>

<div class="abs footer-head" style="left:674px;top:4300px">CONTACT US</div>
<div class="abs" style="left:674px;top:4345px;font-size:14px;line-height:33px;color:var(--white)">
  <div><svg width="10" height="14" fill="#fff" style="margin-right:18px;vertical-align:-2px"><path d="M5 0a5 5 0 0 1 5 5c0 4-5 9-5 9S0 9 0 5a5 5 0 0 1 5-5z"/></svg>United States Office</div>
  <div style="padding-left:33px">1180 Birchmont Avenue, Suite 1400</div>
  <div style="padding-left:33px">Northfield, NY 10488</div>
  <div style="margin-top:33px"><svg width="13" height="10" fill="#fff" style="margin-right:15px;vertical-align:-1px"><rect width="13" height="10" rx="1"/></svg>contact@tollenridgecanvas.com</div>
  <div><svg width="12" height="12" fill="#fff" style="margin-right:16px;vertical-align:-1px"><path d="M2 0l3 0 1 3-2 1a7 7 0 0 0 4 4l1-2 3 1v3C6 10 1 5 2 0z"/></svg>+1 (555) 014-2286</div>
</div>

<div class="abs footer-head" style="left:970px;top:4300px">FOLLOW US</div>
<div class="abs social" style="left:972px;top:4345px"></div>
<div class="abs social" style="left:1008px;top:4345px"></div>
<div class="abs social" style="left:1044px;top:4345px"></div>

<div class="abs" style="left:112px;top:4578px;width:976px;height:1px;background:rgba(255,255,255,.25)"></div>
<div class="abs" style="left:0;width:1200px;text-align:center;top:4602px;font-size:13px;color:var(--white)">(C) Copyright 2026 | All Rights Reserved</div>

</body>
</html>
```